1876 Basins & Spouts Business Card

I'm wanting to get a business card designed. Our business is 1876 Basins & Spouts
Details for the card:

1876 Basins & Spouts
Name: Harold Vesk
Email: harold@1876basinsandspouts.com.au
Website: www.1876basinsandspouts.com.au
Mobile: 0438 260 947
Phone: 02 7481 3926

Font of Basins & Spouts is called Snell Roundhand. Not sue what font logo text is.

I'm thinking two sided but it doesn't have to be.

```html
<!DOCTYPE html>
<html lang="en">
<head>
<meta charset="utf-8">
<title>1876 Basins &amp; Spouts Business Card</title>
<link rel="stylesheet" href="https://fonts.googleapis.com/css2?family=Lato:wght@400;700&family=Montserrat:wght@500&display=swap">
<style>
  :root {
    --backdrop: #161616;
    --card: #222222;
    --card-edge: #2c2c2c;
    --ink-bright: #e6e6e6;
    --ink-soft: #a9a9a9;
    --ink-mark: #8a8a8a;
    --rule: #5a5a5a;
  }
  * { margin: 0; padding: 0; box-sizing: border-box; }
  html, body {
    width: 1200px;
    height: 900px;
    overflow: hidden;
    background: var(--backdrop);
    font-family: "Lato", sans-serif;
  }
  .stage {
    width: 1200px;
    height: 900px;
    display: flex;
    flex-direction: column;
    align-items: center;
    justify-content: center;
    gap: 40px;
  }
  .card {
    width: 700px;
    height: 400px;
    background: linear-gradient(135deg, var(--card) 0%, var(--card-edge) 100%);
    border-radius: 3px;
    position: relative;
  }
  .card-front {
    display: flex;
    align-items: center;
    justify-content: center;
  }
  .brand {
    display: flex;
    align-items: center;
    gap: 14px;
    color: var(--ink-mark);
    font-family: "Lato", sans-serif;
    font-weight: 400;
    letter-spacing: 1px;
  }
  .brand-dot {
    width: 12px;
    height: 12px;
    border-radius: 50%;
    background: var(--ink-mark);
  }
  .card-front .brand { font-size: 34px; }
  .card-back .brand { font-size: 22px; }
  .card-back {
    display: grid;
    grid-template-columns: 330px 1px 1fr;
    align-items: center;
  }
  .back-brand {
    display: flex;
    justify-content: center;
  }
  .divider {
    width: 1px;
    height: 240px;
    background: var(--rule);
  }
  .details {
    padding-left: 28px;
    color: var(--ink-soft);
  }
  .person-name {
    font-family: "Montserrat", sans-serif;
    font-weight: 500;
    font-size: 27px;
    letter-spacing: 3px;
    text-transform: uppercase;
    color: var(--ink-bright);
  }
  .person-role {
    font-size: 16px;
    letter-spacing: 1px;
    margin-bottom: 18px;
  }
  .address {
    font-size: 17px;
    line-height: 1.35;
    letter-spacing: 1px;
    margin-bottom: 14px;
  }
  .contact-list { list-style: none; }
  .contact-list li {
    display: flex;
    align-items: center;
    gap: 10px;
    font-size: 16px;
    letter-spacing: 1px;
    line-height: 1.6;
    color: var(--ink-bright);
  }
  .contact-list svg {
    width: 13px;
    height: 13px;
    flex: none;
    stroke: var(--ink-soft);
    fill: none;
    stroke-width: 1.6;
  }
</style>
</head>
<body>
<main class="stage">
  <section class="card card-front">
    <div class="brand"><span class="brand-dot"></span>1876 Basins &amp; Spouts</div>
  </section>

  <section class="card card-back">
    <div class="back-brand">
      <div class="brand"><span class="brand-dot"></span>1876 Basins &amp; Spouts</div>
    </div>
    <div class="divider"></div>
    <div class="details">
      <h1 class="person-name">Harold Vesk</h1>
      <p class="person-role">Director</p>
      <p class="address">PO Box 41 Mount<br>Ashby NSW 2793</p>
      <ul class="contact-list">
        <li>
          <svg viewBox="0 0 16 16"><path d="M4 1.5l2.5 3-1.5 1.5c.8 2 2.5 3.7 4.5 4.5l1.5-1.5 3 2.5-1.5 2.5C7 14 2 9 1.5 3z"/></svg>
          0438 260 947
        </li>
        <li>
          <svg viewBox="0 0 16 16"><rect x="4" y="1" width="8" height="14" rx="1.5"/><line x1="7" y1="12.5" x2="9" y2="12.5"/></svg>
          02 7481 3926
        </li>
        <li>
          <svg viewBox="0 0 16 16"><rect x="1" y="3" width="14" height="10"/><path d="M1 3l7 6 7-6"/></svg>
          harold@1876basinsandspouts.com.au
        </li>
        <li>
          <svg viewBox="0 0 16 16"><circle cx="8" cy="8" r="6.5"/><ellipse cx="8" cy="8" rx="3" ry="6.5"/><line x1="1.5" y1="8" x2="14.5" y2="8"/></svg>
          www.1876basinsandspouts.com.au
        </li>
      </ul>
    </div>
  </section>
</main>
</body>
</html>
```